Building Referrer Relationships Booklet

4 page A4 booklet to give to potential professional referrers to establish a collaborative relationship.Needs to be bright, vibrant, colourful, friendly, inviting, in keeping with The Linden Practice colours.
Want to provide potential referrer partners a great reason to choose to collaborate with us. They need to know who we are, what makes us different/appealing, and who we are looking for to connect with.
The final product should communicate high performance and connectedness.
Updates

Target Market(s)

professional medical allied health and fitness practitioners

Industry/Entity Type

Health

Requirements
Must have
• energetic, vibrant, engaging, inviting, images

```html
<!DOCTYPE html>
<html lang="en">
<head>
<meta charset="utf-8">
<title>The Linden Practice – Referrer Booklet Spread</title>
<link rel="stylesheet" href="https://fonts.googleapis.com/css2?family=Cinzel:wght@400;700&family=Didact+Gothic&family=EB+Garamond:wght@400;500&display=swap">
<style>
:root{
  --bg:#e4e4e4;
  --paper:#f7f7f7;
  --orange:#d97a16;
  --orange-light:#f0a941;
  --teal:#1fa58e;
  --hex-line:#8fd6cc;
  --hex-green:#6cc57a;
  --rose:#a86b6a;
  --blue:#1ba4e0;
  --ink:#2a2a2a;
  --ink-soft:#444;
}
*{box-sizing:border-box;margin:0;padding:0}
html,body{width:1200px;height:840px;overflow:hidden;background:var(--bg)}
body{font-family:"Didact Gothic",sans-serif;color:var(--ink)}
.spread{position:absolute;left:30px;top:17px;width:1140px;height:806px;display:flex;box-shadow:0 6px 20px rgba(0,0,0,.15)}
.page{position:relative;width:570px;height:806px;background:var(--paper);overflow:hidden}
.page--left{box-shadow:inset -14px 0 18px -14px rgba(0,0,0,.18)}
.page--right{box-shadow:inset 14px 0 18px -14px rgba(0,0,0,.18)}

.band{position:absolute;color:#fff;font-family:"Cinzel",serif;letter-spacing:1px}
.band--about{top:112px;left:0;width:260px;height:40px;background:var(--orange);font-size:17px;text-align:right;padding:9px 18px 0 0}
.band--fix{top:150px;right:0;width:235px;height:66px;background:var(--orange-light);font-size:22px;font-weight:700;padding:18px 0 0 22px}

.values{position:absolute;top:40px;left:276px;width:268px;font-size:10px;line-height:1.3;color:var(--ink-soft)}
.values b{color:#111}
.values-hex{position:absolute;top:222px;left:400px}
.values-hex text{font-family:"EB Garamond",serif;font-size:8.5px;fill:#555;text-anchor:middle}

.photo{position:absolute;background:linear-gradient(135deg,#e9e9ea,#cfd0d2 55%,#b9a696)}
.photo--treatment{top:232px;left:30px;width:360px;height:230px}
.quote{position:absolute;top:392px;left:290px;width:250px;height:140px;background:var(--rose);color:#fff;font-size:13px;line-height:1.45;text-align:center;padding:26px 18px 0}
.quote::before{content:"";position:absolute;top:-10px;left:0;right:0;height:10px;background:var(--orange)}

.loves{position:absolute;top:474px;left:40px;width:238px;font-size:10.5px;line-height:1.3}
.loves p{margin-bottom:10px}
.loves ul{list-style:none}
.loves li{position:relative;padding-left:26px;margin-bottom:8px}
.grid-icon{position:absolute;left:0;top:2px;width:5px;height:5px;background:var(--teal);box-shadow:7px 0 var(--teal),0 7px var(--teal),7px 7px var(--teal)}

.team-rule{position:absolute;height:2px;background:var(--blue)}
.team-title{position:absolute;top:634px;left:408px;font-family:"Cinzel",serif;font-size:22px;color:var(--blue);white-space:nowrap}
.member{position:absolute;width:100px;text-align:center}
.member svg{display:block;margin:0 auto}
.member-name{font-family:"EB Garamond",serif;font-size:9px;line-height:1.15;margin-top:3px}

.corner{position:absolute;top:0;left:0}

.way-title{position:absolute;top:118px;left:40px;width:300px;text-align:center;font-size:17px;letter-spacing:1px;line-height:1.25}
.way-text{position:absolute;top:172px;left:44px;width:290px;font-size:11.5px;line-height:1.35;letter-spacing:.3px}
.collage{position:absolute;top:280px;left:26px;width:300px;height:320px;display:grid;grid-template-columns:1fr 1fr;grid-template-rows:1.1fr 1fr 1fr;gap:4px}
.collage .tile{background:linear-gradient(135deg,#b85a3e,#4a3a33 60%,#a58a6c)}
.collage .tile--wide{grid-column:1/3;background:linear-gradient(135deg,#8b3a2a,#2b2b2b 55%,#b33a2e)}
.collage .tile--tall{grid-row:2/4;grid-column:2;background:linear-gradient(160deg,#ddd8d0,#8a6c50 60%,#5b4a3d)}
.collage .tile--grey{background:linear-gradient(135deg,#d2d0cc,#5b5450)}

.steps{position:absolute;top:226px;left:340px;width:222px;font-size:10.5px;line-height:1.28}
.step{margin-bottom:6px}
.step-head{display:flex;align-items:baseline;gap:6px;font-size:10px;letter-spacing:.5px}
.step-num{font-size:20px;line-height:1}
.step-sub{font-family:"EB Garamond",serif;font-size:7.5px;display:block;margin-left:30px;color:#555}
.step ul{list-style:none;font-family:"EB Garamond",serif;font-size:10.5px}
.step li{position:relative;padding-left:14px}
.step li .grid-icon{width:3px;height:3px;top:5px;box-shadow:4px 0 var(--teal),0 4px var(--teal),4px 4px var(--teal)}
</style>
</head>
<body>
<div class="spread">

  <section class="page page--left">
    <div class="band band--about">ABOUT US</div>

    <p class="values"><b>COURAGE</b> gives us the strength and confidence to take risks and embrace challenges. <b>INSPIRATION</b> is our energy, our fuel for success, that life force that feeds us as we grow and develop. <b>FUN</b> generates happiness, and we all function at our best when we are happy. <b>CREATIVITY</b> sets us as an innovative leading-edge business. <b>WOW</b> means being the very best we can be and realise our true potential. We are not your average business, our service is not average, and our people are not average. <b>TEAM</b> and in particular high-performance team means we perform at our very best. Great teamwork creates unity and we accomplish much more than each of us alone.</p>

    <svg class="values-hex" width="160" height="136" viewBox="0 0 200 170" aria-label="Our values">
      <g stroke="var(--hex-line)" stroke-width="3">
        <polygon points="20,5 50,5 65,31 50,57 20,57 5,31" fill="#fff"/>
        <polygon points="70,33 100,33 115,59 100,85 70,85 55,59" fill="var(--hex-green)"/>
        <polygon points="20,61 50,61 65,87 50,113 20,113 5,87" fill="#fff"/>
        <polygon points="120,61 150,61 165,87 150,113 120,113 105,87" fill="#fff"/>
        <polygon points="70,89 100,89 115,115 100,141 70,141 55,115" fill="#fff"/>
        <polygon points="20,117 50,117 65,143 50,169 20,169 5,143" fill="var(--hex-green)"/>
      </g>
      <text x="35" y="34">COURAGE</text>
      <text x="85" y="62" fill="#fff">INSPIRATION</text>
      <text x="35" y="90">CREATIVE</text>
      <text x="135" y="90">FUN</text>
      <text x="85" y="118">WOW</text>
      <text x="35" y="146">TEAM</text>
    </svg>

    <div class="photo photo--treatment" role="img" aria-label="Podiatrist in mask and gloves treating a smiling patient's foot in a bright clinic"></div>
    <div class="quote">At The Linden Practice, we are passionate about building strong postural foundations, from the feet up.</div>

    <div class="loves">
      <p>The top 3 things our clients love about us (and hopefully yours will too!):</p>
      <ul>
        <li><span class="grid-icon"></span>Positive energy, enthusiasm and outcomes NPS average score &gt;9 out of 10</li>
        <li><span class="grid-icon"></span>Trusted leader in the practice of podiatric medicine established 1999, elite experience, latest high-tech equipment</li>
        <li><span class="grid-icon"></span>Focus is on strong feet, not just orthotics! Barefoot Motion Training, Fascial Line Therapy, Foot Manual Therapies</li>
      </ul>
    </div>

    <div class="team-rule" style="left:290px;top:650px;width:110px"></div>
    <div class="team-title">OUR TEAM</div>

    <div class="member" style="left:268px;top:668px">
      <svg width="84" height="74" viewBox="0 0 84 74"><polygon points="21,3 63,3 82,37 63,71 21,71 2,37" fill="#9aa5a8" stroke="var(--hex-line)" stroke-width="4" role="img" aria-label="Portrait of principal podiatrist"/></svg>
      <div class="member-name">Dr Marcus Delaine<br>(Principal Podiatrist)</div>
    </div>
    <div class="member" style="left:363px;top:668px">
      <svg width="84" height="74" viewBox="0 0 84 74"><polygon points="21,3 63,3 82,37 63,71 21,71 2,37" fill="#7d8b8c" stroke="#3fae5a" stroke-width="4" role="img" aria-label="Portrait of senior podiatrist"/></svg>
      <div class="member-name">Dr Fiona Castell<br>(Senior Podiatrist)</div>
    </div>
    <div class="member" style="left:458px;top:668px">
      <svg width="84" height="74" viewBox="0 0 84 74"><polygon points="21,3 63,3 82,37 63,71 21,71 2,37" fill="#b0aaa6" stroke="#f4e11c" stroke-width="4" role="img" aria-label="Portrait of podiatrist"/></svg>
      <div class="member-name">Dr Isla Brandt<br>(Podiatrist)</div>
    </div>
  </section>

  <section class="page page--right">
    <svg class="corner" width="90" height="60" viewBox="0 0 90 60"><polygon points="0,0 90,0 0,60" fill="var(--orange)"/></svg>
    <div class="band band--fix">FIX YOUR FEET</div>

    <h2 class="way-title">THE<br>LINDEN PRACTICE WAY</h2>
    <p class="way-text">Our pathway to strengthen postural foundations, to create lasting changes for freedom of movement, and ultimately keep us going well beyond what we thought was possible (updated as research and tech changes).</p>

    <div class="collage">
      <div class="tile tile--wide" role="img" aria-label="Group of smiling workshop attendees in a studio with a red wall"></div>
      <div class="tile tile--grey" role="img" aria-label="Presenter demonstrating movement to a seated group"></div>
      <div class="tile tile--tall" role="img" aria-label="Large group moving barefoot on a wooden studio floor"></div>
      <div class="tile" role="img" aria-label="Two presenters speaking at the front of a workshop room"></div>
    </div>

    <div class="steps">
      <div class="step">
        <div class="step-head"><span class="step-num">01</span>FIX THE PAIN</div>
        <ul>
          <li><span class="grid-icon"></span>Provide analgesia</li>
          <li><span class="grid-icon"></span>Reduce inflammation</li>
          <li><span class="grid-icon"></span>Corn/callus/foreign body removal</li>
          <li><span class="grid-icon"></span>Ingrown/thickened toenail repair and maintenance</li>
          <li><span class="grid-icon"></span>Surgery</li>
        </ul>
      </div>
      <div class="step">
        <div class="step-head"><span class="step-num">02</span>PROTECT THE FEET</div>
        <span class="step-sub">(reduce damage, optimise stability, promote healing)</span>
        <ul>
          <li><span class="grid-icon"></span>Reduce tissue damage</li>
          <li><span class="grid-icon"></span>Optimise Foot Posture</li>
          <li><span class="grid-icon"></span>Activate neuromuscular/reflexive balance stability</li>
          <li><span class="grid-icon"></span>Promote tissue repair/cellular regeneration</li>
        </ul>
      </div>
      <div class="step">
        <div class="step-head"><span class="step-num">03</span>STRENGTHEN THE FEET</div>
        <span class="step-sub">(increase strength and resilience)</span>
        <ul>
          <li><span class="grid-icon"></span>Strengthen intrinsics</li>
          <li><span class="grid-icon"></span>Connect foot strength to core strength</li>
          <li><span class="grid-icon"></span>Stimulate neuromuscular strength</li>
          <li><span class="grid-icon"></span>Biohack Your Body</li>
        </ul>
      </div>
      <div class="step">
        <div class="step-head"><span class="step-num">04</span>PROTECT THE WHOLE BODY</div>
        <span class="step-sub">(stability)</span>
        <ul>
          <li><span class="grid-icon"></span>Optimise Postural Alignment</li>
          <li><span class="grid-icon"></span>Activate neuromuscular/reflexive balance stability</li>
          <li><span class="grid-icon"></span>Customised corrective exercises</li>
          <li><span class="grid-icon"></span>Improve cellular regeneration</li>
          <li><span class="grid-icon"></span>Optimise nutrition/healthy gut</li>
          <li><span class="grid-icon"></span>Optimise healthy mind</li>
        </ul>
      </div>
      <div class="step">
        <div class="step-head"><span class="step-num">05</span>STRENGTHEN THE WHOLE BODY</div>
        <span class="step-sub">(strength, elasticity)</span>
        <ul>
          <li><span class="grid-icon"></span>Strengthen the deep core (stabilisers)</li>
          <li><span class="grid-icon"></span>Strengthen the outer core (mobilisers)</li>
          <li><span class="grid-icon"></span>Increase fascial elasticity/strength</li>
          <li><span class="grid-icon"></span>Increase functional strength</li>
          <li><span class="grid-icon"></span>Increase endurance</li>
          <li><span class="grid-icon"></span>Customised nutrition for specific performance</li>
          <li><span class="grid-icon"></span>Improve psychological resilience</li>
        </ul>
      </div>
      <div class="step">
        <div class="step-head"><span class="step-num">06</span>REPEAT CONSISTENTLY</div>
      </div>
    </div>

    <div class="team-rule" style="left:0;width:320px;top:650px"></div>

    <div class="member" style="left:6px;top:668px">
      <svg width="84" height="74" viewBox="0 0 84 74"><polygon points="21,3 63,3 82,37 63,71 21,71 2,37" fill="#8fa0b5" stroke="#223a8c" stroke-width="4" role="img" aria-label="Portrait of podiatrist"/></svg>
      <div class="member-name">Dr Peter Vance<br>(Podiatrist)</div>
    </div>
    <div class="member" style="left:106px;top:668px">
      <svg width="84" height="74" viewBox="0 0 84 74"><polygon points="21,3 63,3 82,37 63,71 21,71 2,37" fill="#a89a8e" stroke="#d62631" stroke-width="4" role="img" aria-label="Portrait of practice manager"/></svg>
      <div class="member-name">Carla Whitby<br>(Practice Manager)</div>
    </div>
    <div class="member" style="left:206px;top:668px">
      <svg width="84" height="74" viewBox="0 0 84 74"><polygon points="21,3 63,3 82,37 63,71 21,71 2,37" fill="#8e6f66" stroke="#d62631" stroke-width="4" role="img" aria-label="Portrait of front office administrator"/></svg>
      <div class="member-name">Nina Hollis<br>(Front Office Administrator)</div>
    </div>
  </section>

</div>
</body>
</html>
```